Card design for orthopaedic surgeons working as The Brightwater Joint Centre

Business cards, letterhead

Colors

Designer to choose colors to be used in the design.

Requirements
Must have
• Late addition.
• Cards letterhead must have logos of
• Crestmoor Lindell College of Surgeons
• Varenwood Bone Health Association
Nice to have
• Back of card to have space for appointment time to be added by hand and some blank space for writing incidental other notes.

```html
<!DOCTYPE html>
<html lang="en">
<head>
<meta charset="utf-8">
<title>The Brightwater Joint Centre – Business Card</title>
<link rel="stylesheet" href="https://fonts.googleapis.com/css2?family=Open+Sans:wght@400;600&family=Arimo:wght@700&display=swap">
<style>
  :root {
    --page-bg: #e9ebee;
    --sky: #36b0f8;
    --navy: #0e3450;
    --ink: #1d2730;
    --paper: #ffffff;
    --rule: #b9c2c9;
    --badge: rgba(255,255,255,0.55);
  }
  * { box-sizing: border-box; margin: 0; padding: 0; }
  html, body { width: 1200px; height: 960px; overflow: hidden; }
  body {
    background: var(--page-bg);
    font-family: "Open Sans", Arial, sans-serif;
    position: relative;
  }
  .card {
    position: absolute;
    left: 250px;
    width: 700px;
    height: 400px;
    overflow: hidden;
    box-shadow: 0 6px 24px rgba(0,0,0,0.18);
  }
  .card-back { top: 50px; background: var(--sky); }
  .card-front { top: 500px; background: var(--paper); }

  .back-brand {
    position: absolute; top: 150px; left: 0; width: 100%;
    text-align: center; color: var(--paper);
    font-size: 38px; font-weight: 400; letter-spacing: -0.5px;
  }
  .back-web {
    position: absolute; top: 222px; left: 0; width: 100%;
    text-align: center; color: var(--paper);
    font-size: 18px; letter-spacing: 4px;
  }
  .affiliations {
    position: absolute; right: 32px; bottom: 28px;
    display: flex; gap: 14px; list-style: none;
  }
  .affiliation-badge {
    width: 38px; height: 38px; border-radius: 50%;
    background: var(--badge);
  }

  .front-art { position: absolute; inset: 0; }
  .front-brand {
    position: absolute; top: 66px; right: 40px;
    color: var(--sky); font-size: 32px; font-weight: 400; letter-spacing: -0.4px;
    white-space: nowrap;
  }
  .person-name {
    position: absolute; top: 112px; left: 40px;
    font-family: "Arimo", Arial, sans-serif; font-weight: 700;
    font-size: 22px; color: var(--navy);
  }
  .person-title {
    position: absolute; top: 142px; left: 40px;
    font-size: 16px; color: var(--sky);
  }
  .contact-list {
    position: absolute; top: 196px; left: 40px; list-style: none;
    font-size: 15px; color: var(--ink);
  }
  .contact-list li { display: flex; align-items: center; gap: 10px; height: 28px; }
  .contact-list svg { width: 14px; height: 14px; }
  .address {
    position: absolute; top: 200px; left: 330px;
    padding-left: 22px; border-left: 1.5px solid var(--rule);
    font-size: 15px; line-height: 26px; color: var(--ink); font-style: normal;
  }
  .front-web {
    position: absolute; bottom: 16px; right: 36px;
    color: var(--paper); font-size: 17px; letter-spacing: 2px; font-weight: 600;
  }
</style>
</head>
<body>
  <section class="card card-back" aria-label="Card back">
    <p class="back-brand">The Brightwater Joint Centre</p>
    <p class="back-web">www.brightwaterjoint.com</p>
    <ul class="affiliations">
      <li class="affiliation-badge" role="img" aria-label="Crestmoor Lindell College of Surgeons badge"></li>
      <li class="affiliation-badge" role="img" aria-label="Varenwood Bone Health Association badge"></li>
    </ul>
  </section>

  <section class="card card-front" aria-label="Card front">
    <svg class="front-art" width="700" height="400" viewBox="0 0 700 400" aria-hidden="true">
      <line x1="92" y1="152" x2="700" y2="152" stroke="#36b0f8" stroke-width="2"/>
      <polygon points="0,286 262,286 296,326 288,330 256,294 0,294" fill="#36b0f8"/>
      <polygon points="0,300 258,300 290,340 700,340 700,400 0,400" fill="#0e3450"/>
    </svg>

    <p class="front-brand">The Brightwater Joint Centre</p>
    <h1 class="person-name">Nora Ellison</h1>
    <p class="person-title">Title</p>

    <ul class="contact-list">
      <li>
        <svg viewBox="0 0 14 14" aria-hidden="true"><path d="M3 1.5 L5.2 1.5 L6 4.5 L4.6 5.6 Q5.6 8.2 8.4 9.4 L9.5 8 L12.5 8.8 L12.5 11 Q12.5 12.5 11 12.5 Q2 12 1.5 3 Q1.5 1.5 3 1.5Z" fill="#36b0f8"/></svg>
        012-345-6789
      </li>
      <li>
        <svg viewBox="0 0 14 14" aria-hidden="true"><rect x="1" y="3" width="12" height="8" rx="1" fill="#36b0f8"/><path d="M1.5 3.5 L7 7.5 L12.5 3.5" stroke="#fff" stroke-width="1.2" fill="none"/></svg>
        info@brightwaterjoint.com
      </li>
    </ul>

    <address class="address">
      Street Name, City Name<br>
      Zipcode - 012345
    </address>

    <p class="front-web">www.brightwaterjoint.com</p>
  </section>
</body>
</html>
```